Employee Benefits and Insurance Consulting

We are an existing company with over 30 years experience but are changing our name. We would like a simple design with grey tones.

Industry/Entity Type

Insurance

Contact Information for Business Card

Marlow Benefits Consulting
Gerald P Hollins CEO
5172 Brackenridge Road
Halden Springs, TN 37990
gerald@marlowbenefits-example.com
865-412-5593 - O
865-247-3861 - C

```html
<!DOCTYPE html>
<html lang="en">
<head>
<meta charset="UTF-8">
<title>Marlow Benefits Consulting – Business Card</title>
<link rel="stylesheet" href="https://fonts.googleapis.com/css2?family=Marcellus&family=Roboto:wght@300;400&display=swap">
<style>
  :root {
    --backdrop: #d6d8da;
    --card: #eef0f1;
    --brand-blue: #29abe2;
    --band-grey: #8f8f8f;
    --ink-grey: #6d6e70;
    --ink-dark: #58595b;
    --divider: #a9acae;
  }
  * { margin: 0; padding: 0; box-sizing: border-box; }
  html, body {
    width: 1200px;
    height: 901px;
    overflow: hidden;
    background: var(--backdrop);
  }
  .stage {
    width: 1200px;
    height: 901px;
    display: flex;
    align-items: center;
    justify-content: center;
  }
  .card {
    position: relative;
    width: 1040px;
    height: 580px;
    background: var(--card);
    box-shadow: 0 8px 22px rgba(0,0,0,0.2);
    overflow: hidden;
  }
  .band {
    position: absolute;
    width: 50%;
    height: 40px;
  }
  .band--top { top: 0; }
  .band--bottom { bottom: 0; }
  .band--left { left: 0; }
  .band--right { right: 0; }
  .band--grey { background: var(--band-grey); }
  .band--blue { background: var(--brand-blue); }
  .card__divider {
    position: absolute;
    left: 50%;
    top: 62px;
    bottom: 62px;
    width: 2px;
    background: var(--divider);
  }
  .panel {
    position: absolute;
    top: 40px;
    bottom: 40px;
    width: 50%;
  }
  .panel--brand { left: 0; }
  .panel--contact { right: 0; }

  /* Logo panel */
  .brand {
    position: absolute;
    inset: 0;
    display: flex;
    flex-direction: column;
    align-items: center;
    justify-content: center;
    font-family: "Marcellus", serif;
    color: var(--ink-grey);
  }
  .brand__mark {
    width: 44px;
    height: 44px;
    border-radius: 50%;
    background: var(--brand-blue);
    margin-bottom: 18px;
  }
  .brand__name {
    font-size: 104px;
    line-height: 1;
  }
  .brand__tagline {
    font-size: 26px;
    letter-spacing: 2px;
    margin-top: 6px;
  }

  /* Contact panel */
  .contact {
    position: absolute;
    top: 70px;
    right: 60px;
    left: 60px;
    display: flex;
    flex-direction: column;
    align-items: flex-end;
    font-family: "Roboto", sans-serif;
    font-weight: 300;
    color: var(--ink-dark);
  }
  .contact__name {
    font-family: "Marcellus", serif;
    font-weight: 400;
    font-size: 36px;
    color: var(--ink-grey);
  }
  .contact__title {
    font-size: 18px;
    font-style: italic;
    color: var(--brand-blue);
    margin: 2px 110px 40px 0;
  }
  .contact__list {
    list-style: none;
    font-size: 19px;
    line-height: 1.6;
    align-self: flex-start;
    margin-left: 60px;
  }
  .contact__item {
    display: flex;
    align-items: center;
    gap: 10px;
  }
  .contact__icon {
    width: 18px;
    height: 18px;
    flex: none;
  }
  .contact__address {
    font-style: normal;
    font-size: 19px;
    line-height: 1.55;
    margin-top: 34px;
    align-self: flex-start;
    margin-left: 30px;
  }
</style>
</head>
<body>
<main class="stage">
  <section class="card" aria-label="Business card">
    <div class="band band--top band--left band--grey"></div>
    <div class="band band--top band--right band--blue"></div>

    <div class="panel panel--brand">
      <div class="brand">
        <span class="brand__mark" aria-hidden="true"></span>
        <span class="brand__name">Marlow</span>
        <span class="brand__tagline">Benefits Consulting</span>
      </div>
    </div>

    <div class="card__divider" aria-hidden="true"></div>

    <div class="panel panel--contact">
      <div class="contact">
        <h1 class="contact__name">Gerald P Hollins</h1>
        <p class="contact__title">(CEO)</p>
        <ul class="contact__list">
          <li class="contact__item">
            <svg class="contact__icon" viewBox="0 0 16 16" aria-hidden="true">
              <rect x="4" y="1" width="8" height="14" rx="1.5" fill="none" stroke="#29abe2" stroke-width="1.6"/>
              <circle cx="8" cy="12.3" r="0.9" fill="#29abe2"/>
            </svg>
            865-247-3861
          </li>
          <li class="contact__item">
            <svg class="contact__icon" viewBox="0 0 16 16" aria-hidden="true">
              <circle cx="8" cy="8" r="8" fill="#29abe2"/>
              <path d="M5.3 4.2c.4-.3.9-.2 1.1.2l.7 1.3c.2.4.1.8-.2 1l-.5.4c.4.9 1 1.6 1.9 2.1l.4-.5c.3-.3.7-.4 1-.2l1.3.7c.4.2.5.7.2 1.1l-.6.8c-.4.4-1 .5-1.5.3-2.1-.9-3.6-2.5-4.4-4.6-.2-.5 0-1.1.4-1.5z" fill="#fff"/>
            </svg>
            865-412-5593
          </li>
          <li class="contact__item">
            <svg class="contact__icon" viewBox="0 0 16 16" aria-hidden="true">
              <rect x="1" y="3.5" width="14" height="9" rx="1" fill="#29abe2"/>
              <path d="M1.5 4.2 8 9l6.5-4.8" fill="none" stroke="#fff" stroke-width="1.1"/>
            </svg>
            gerald@marlowbenefits-example.com
          </li>
        </ul>
        <address class="contact__address">
          5172 Brackenridge Road<br>
          Halden Springs, TN 37990
        </address>
      </div>
    </div>

    <div class="band band--bottom band--left band--blue"></div>
    <div class="band band--bottom band--right band--grey"></div>
  </section>
</main>
</body>
</html>
```